Coral Bay Pools New website

I currently operate a swimming pool service and repair business and looking for a re design for my website as it has been over 5 years since it was designed. current site is coralbaypoolslv.com

```html
<!DOCTYPE html>
<html lang="en">
<head>
<meta charset="utf-8">
<title>Coral Bay Pools</title>
<link href="https://fonts.googleapis.com/css2?family=Outfit:wght@300;400;500;600;700&display=swap" rel="stylesheet">
<style>
:root{
  --black:#000;
  --panel:#0f0f0f;
  --white:#fff;
  --blue:#1a6db0;
  --blue-dark:#11518a;
  --orange:#f7941d;
  --grey:#d8d8d8;
  --line:#2a2a2a;
}
*{margin:0;padding:0;box-sizing:border-box}
html,body{width:1200px;height:3051px;overflow:hidden;background:var(--black)}
body{position:relative;font-family:'Outfit',sans-serif;color:var(--white)}
.abs{position:absolute}
/* hero */
.hero{left:0;top:0;width:1200px;height:540px;background:linear-gradient(135deg,#2f6f86 0%,#3a8fa6 40%,#2b7c97 70%,#1f5f78 100%)}
.hero-wave{left:0;top:500px;width:1200px;height:45px}
.brand{left:112px;top:40px;display:flex;align-items:center;gap:10px;font-size:20px;font-weight:600;color:var(--white)}
.brand-dot{width:18px;height:18px;border-radius:50%;background:var(--orange)}
.nav{left:388px;top:50px;width:531px;height:40px;background:var(--white);border-radius:20px;display:flex;align-items:center;justify-content:space-around;padding:0 12px;font-size:13px;color:#111}
.nav .active{color:var(--blue);position:relative}
.nav .active:after{content:"";position:absolute;left:0;right:0;bottom:-8px;height:2px;background:var(--blue)}
.phone-pill{left:934px;top:50px;width:154px;height:40px;border:1px solid rgba(255,255,255,.7);border-radius:20px;display:flex;align-items:center;gap:12px;padding-left:6px;font-size:13px}
.phone-pill .ico{width:28px;height:28px;border-radius:50%;background:var(--blue);display:flex;align-items:center;justify-content:center}
.center{left:0;width:1200px;text-align:center}
.kicker{font-size:16px;font-weight:500;letter-spacing:.2px}
.hero-title{top:200px;font-size:41px;font-weight:600;line-height:57px;letter-spacing:-1.5px}
.hero-title .hl{background:var(--blue-dark);padding:0 4px}
.hero-sub{top:330px;font-size:16px;font-weight:300}
.btn{display:flex;align-items:center;justify-content:center;border-radius:22px;font-size:14px;font-weight:500;background:var(--blue);color:var(--white)}
.btn.outline{background:transparent;border:1px solid var(--blue)}
/* services */
.h2{font-size:41px;font-weight:600;line-height:57px;letter-spacing:-1.5px}
.orange{color:var(--orange)}
.card{top:826px;width:317px;height:362px;border:1px solid #2a2a2a;border-radius:8px;background:#050505;overflow:hidden}
.card-img{position:absolute;left:6px;top:7px;width:305px;height:292px}
.card-badge{position:absolute;left:50%;top:237px;width:74px;height:74px;margin-left:-37px;border-radius:50%;background:var(--blue);border:5px solid #0a0a0a;display:flex;align-items:center;justify-content:center}
.card-title{position:absolute;left:0;right:0;top:320px;text-align:center;font-size:20px;font-weight:500}
.card-bar{position:absolute;left:20px;right:20px;bottom:0;height:4px;background:var(--blue);border-radius:2px}
/* about */
.about-text{left:113px;top:1553px;width:483px;font-size:16px;font-weight:300;line-height:34.3px;text-align:justify}
.about-accent{left:944px;top:1780px;width:152px;height:178px;background:var(--blue);border-radius:4px}
.about-img{left:659px;top:1400px;width:429px;height:549px;border-radius:4px;background:linear-gradient(160deg,#b9c8b8 0%,#3fa8c8 45%,#3cc2e0 100%)}
/* why */
.why{left:0;top:2050px;width:1200px;height:495px;background:linear-gradient(90deg,#6d6a58 0%,#4e4c40 40%,#1c1b17 70%,#0b0b0a 100%)}
.why-wave{left:0;top:2045px;width:1200px;height:40px}
.why-text{left:599px;top:2247px;width:489px;font-size:16px;font-weight:300;line-height:34.3px;text-align:justify}
/* footer */
.footer-panel{left:390px;top:2545px;width:419px;height:420px;background:var(--panel)}
.f-head{font-size:21px;font-weight:600;color:var(--orange);letter-spacing:-.5px}
.f-links{left:112px;top:2687px;list-style:none;font-size:14px;font-weight:500;line-height:37px}
.f-about{left:884px;top:2685px;width:210px;font-size:15px;font-weight:300;line-height:33px}
.f-contact{left:423px;font-size:14px;font-weight:500;display:flex;align-items:center;gap:24px}
.f-rule{left:108px;top:2966px;width:984px;height:1px;background:var(--line)}
.to-top{left:584px;top:2950px;width:32px;height:32px;border-radius:50%;background:var(--blue);display:flex;align-items:center;justify-content:center}
.copy{top:3010px;font-size:14px;font-weight:500}
</style>
</head>
<body>

<!-- HERO -->
<div class="abs hero" role="img" aria-label="Aerial view of a woman in a sun hat relaxing at the edge of a sparkling blue pool"></div>
<svg class="abs hero-wave" viewBox="0 0 1200 45" preserveAspectRatio="none"><path d="M0 20 C60 5 110 30 170 22 S280 5 340 20 S460 35 520 18 S640 8 700 24 S820 35 880 18 S1000 5 1060 22 S1160 30 1200 15 L1200 45 L0 45Z" fill="#000"/></svg>

<div class="abs brand"><span class="brand-dot"></span>Coral Bay Pools</div>
<nav class="abs nav"><span class="active">HOME</span><span>ABOUT US</span><span>OUR SERVICES</span><span>FREE ESTIMATE</span><span>CONTACT</span></nav>
<div class="abs phone-pill"><span class="ico"><svg width="13" height="13" viewBox="0 0 24 24"><path d="M6.6 10.8a15 15 0 006.6 6.6l2.2-2.2a1 1 0 011-.25 11.4 11.4 0 003.6.6 1 1 0 011 1V20a1 1 0 01-1 1A17 17 0 013 4a1 1 0 011-1h3.5a1 1 0 011 1c0 1.25.2 2.45.6 3.6a1 1 0 01-.25 1z" fill="#fff"/></svg></span>(702) 555-0148</div>

<div class="abs center kicker" style="top:152px">CORAL BAY POOLS</div>
<h1 class="abs center hero-title">WELCOME <span class="hl">NEVADA’S</span> TOP RATED<br>LOCAL POOL CLEANING</h1>
<p class="abs center hero-sub">We are a full service pool company servicing the Las Vegas Valley.</p>
<a class="abs btn" style="left:502px;top:396px;width:196px;height:44px">FREE ESTIMATE NOW</a>

<!-- SERVICES -->
<svg class="abs" style="left:578px;top:604px" width="44" height="38" viewBox="0 0 44 38" fill="none" stroke="#1a6db0" stroke-width="2"><path d="M4 30c4 3 8 3 12 0s8-3 12 0 8 3 12 0"/><path d="M4 36c4 3 8 3 12 0s8-3 12 0 8 3 12 0"/><circle cx="16" cy="8" r="4"/><path d="M12 24l6-10 8 4 6-6"/></svg>
<h2 class="abs center h2" style="top:661px">EXPLORE OUR<br><span class="orange">CORAL BAY SERVICES</span></h2>

<div class="abs card" style="left:111px">
  <div class="card-img" role="img" aria-label="Technician in blue overalls brushing a pool" style="background:linear-gradient(160deg,#7a6a5c 0%,#6d7a4e 40%,#3a8fc0 80%,#2c9bd6 100%)"></div>
  <div class="card-badge"><svg width="34" height="30" viewBox="0 0 34 30" fill="none" stroke="#fff" stroke-width="2"><path d="M2 22c4 3 8 3 12 0s8-3 12 0"/><circle cx="12" cy="6" r="3"/><path d="M8 18l5-8 7 3 5-5"/></svg></div>
  <div class="card-title">POOL SERVICES</div><div class="card-bar"></div>
</div>
<div class="abs card" style="left:441px">
  <div class="card-img" role="img" aria-label="Contractor in a hard hat reviewing plans beside a resort pool" style="background:linear-gradient(160deg,#4a8cd0 0%,#8cb8e0 45%,#d9e6f0 70%,#3ab6d8 100%)"></div>
  <div class="card-badge"><svg width="34" height="30" viewBox="0 0 34 30" fill="none" stroke="#fff" stroke-width="2"><path d="M5 12a12 8 0 0124 0z"/><path d="M17 12v10"/><path d="M3 26h28"/><path d="M8 22h18"/></svg></div>
  <div class="card-title">COMMERCIAL POOLS</div><div class="card-bar"></div>
</div>
<div class="abs card" style="left:771px">
  <div class="card-img" role="img" aria-label="Pool inspector writing notes at the edge of a residential pool" style="background:linear-gradient(160deg,#6b8aa8 0%,#2f6fb8 45%,#2a9ad8 100%)"></div>
  <div class="card-badge"><svg width="32" height="30" viewBox="0 0 32 30" fill="none" stroke="#fff" stroke-width="2"><path d="M3 14L16 3l13 11"/><path d="M7 11v16h18V11"/><rect x="13" y="18" width="6" height="9"/></svg></div>
  <div class="card-title">RESIDENTIAL POOLS</div><div class="card-bar"></div>
</div>

<a class="abs btn" style="left:411px;top:1246px;width:187px;height:42px">GET A QUOTE FREE!</a>
<a class="abs btn outline" style="left:617px;top:1246px;width:172px;height:42px">LEARN ABOUT US</a>

<!-- ABOUT -->
<div class="abs kicker" style="left:112px;top:1372px">CORAL BAY POOLS</div>
<h2 class="abs h2" style="left:113px;top:1417px">ABOUT<br><span class="orange">CORAL BAY POOLS</span></h2>
<p class="abs about-text">When you need professional pool cleaning services in Nevada, you can count on the professionals at Coral Bay Pools to provide you with superior and prompt solutions. Whether you need assistance with a residential or commercial pool, we’ll vacuum, brush, and thoroughly clean your pool so it’s swim-ready. We’ll also clean your pool filters and inform you of any issues that arise. Our staff is certified by the Regional Water Health Board to ensure proper chemical levels and equipment are safe. To learn more about our pool cleaning services or to get your free estimate, contact our pool experts today.</p>
<a class="abs btn" style="left:113px;top:1927px;width:144px;height:42px">LEARN MORE</a>
<div class="abs about-accent"></div>
<div class="abs about-img" role="img" aria-label="Pool technician leaning over to inspect an above-ground pool liner"></div>

<!-- WHY -->
<div class="abs why" role="img" aria-label="Resort pool with stone edging and landscaped planters at dusk"></div>
<svg class="abs why-wave" viewBox="0 0 1200 40" preserveAspectRatio="none"><path d="M0 0 L1200 0 L1200 20 C1140 30 1090 8 1030 18 S910 32 850 16 S730 5 670 20 S550 32 490 16 S370 4 310 20 S190 32 130 15 S40 8 0 20Z" fill="#000"/></svg>
<div class="abs kicker" style="left:599px;top:2136px">CORAL BAY POOLS</div>
<h2 class="abs h2" style="left:599px;top:2173px">WHY <span class="orange">CHOOSE US</span></h2>
<p class="abs why-text">Our full-service pool company proudly serves the entire Las Vegas valley, and we’re certified by the Regional Water Health Board to maintain the highest level of pool safety. If you need repairs, maintenance, scheduled cleanings, or any other pool services, contact us online or by phone today.</p>
<a class="abs btn" style="left:599px;top:2445px;width:145px;height:43px">CONTACT US</a>

<!-- FOOTER -->
<div class="abs footer-panel"></div>
<div class="abs f-head" style="left:112px;top:2641px">QUICK LINKS</div>
<ul class="abs f-links"><li>HOME</li><li>ABOUT US</li><li>OUR SERVICES</li><li>FREE ESTIMATE</li><li>CONTACT</li><li>BLOG</li><li>PRIVACY POLICY</li></ul>

<div class="abs center" style="top:2680px;font-size:30px;font-weight:600;display:flex;justify-content:center;align-items:center;gap:12px"><span class="brand-dot" style="width:24px;height:24px"></span>Coral Bay Pools</div>
<div class="abs f-contact" style="top:2830px"><svg width="14" height="14" viewBox="0 0 24 24"><path d="M6.6 10.8a15 15 0 006.6 6.6l2.2-2.2a1 1 0 011-.25 11.4 11.4 0 003.6.6 1 1 0 011 1V20a1 1 0 01-1 1A17 17 0 013 4a1 1 0 011-1h3.5a1 1 0 011 1c0 1.25.2 2.45.6 3.6a1 1 0 01-.25 1z" fill="#1a6db0"/></svg>(702) 555-0148</div>
<div class="abs f-contact" style="top:2877px"><svg width="16" height="12" viewBox="0 0 16 12"><rect x="0.5" y="0.5" width="15" height="11" fill="#1a6db0"/><path d="M1 1l7 6 7-6" stroke="#0f0f0f" fill="none"/></svg>POOLSOLUTIONS@CORALBAYPOOLSLV.COM</div>

<div class="abs f-head" style="left:884px;top:2641px">CORAL BAY</div>
<p class="abs f-about">When you invested in your pool, you knew it was a long-term investment in both money and time. At home, it’s an oasis, a place to beat the heat and relax.</p>

<div class="abs f-rule"></div>
<div class="abs to-top"><svg width="14" height="14" viewBox="0 0 14 14" fill="none" stroke="#fff" stroke-width="2"><path d="M7 13V2M2 7l5-5 5 5"/></svg></div>
<div class="abs center copy">©2026 CORAL BAY POOLS - DO NOT COPY. ALL RIGHTS RESERVED</div>

</body>
</html>
```